Automotive component supplier needs a business card design

We need a business card design for our company called Velran Global Components Ltd based in the UK. We are a supplier of interior and exterior components to premium car manufacturers such as Corvel Ashby, Hadley Fenn, Marquist and Tavarelli. We would like to see a modern business card design that uses the colour blue.

Target Market(s)

Premium automotive car manufacturers.

Industry/Entity Type

Automotive

Contact Information for Business Card

Company Name : Velran Global Components Limited
Address: 17 Marlow Yard, Upper Heath, Warwick, CV31 8QL, United Kingdom
Web Address : www.velrancomponents-example.co.uk

Font styles to use
Other font styles liked:
• Helvetica

Colors
3176b5
0255a3
85acd3
cfdeed
cee9f5
85cae6
34a6d7
0692cd
9bcb3c

Requirements
Must have
• Clear company logo and a mixture of blue colours.
Nice to have
• A high quality modern image.
Should not have
• Multiple colours.

```html
<!DOCTYPE html>
<html lang="en">
<head>
<meta charset="utf-8">
<title>Velran Global Components – Business Card</title>
<link rel="stylesheet" href="https://fonts.googleapis.com/css2?family=Arimo:wght@400;700&display=swap">
<style>
  :root{
    --blue-main:#0692cd;
    --blue-deep:#0255a3;
    --blue-mid:#3176b5;
    --blue-bright:#34a6d7;
    --green:#9bcb3c;
    --ink:#5a5f66;
    --paper:#ffffff;
    --backdrop:#e9ecef;
  }
  *{box-sizing:border-box;margin:0;padding:0}
  html,body{width:1200px;height:950px;overflow:hidden}
  body{background:var(--backdrop);font-family:"Arimo",Helvetica,Arial,sans-serif;position:relative}
  .card{position:absolute;left:250px;width:700px;height:400px;overflow:hidden;box-shadow:0 6px 18px rgba(0,0,0,.18)}
  .card--front{top:45px;background:var(--paper)}
  .card--back{top:505px;background:var(--blue-main)}

  .front-band{position:absolute;left:0;top:0;width:700px;height:400px}
  .web-front{position:absolute;right:18px;bottom:16px;color:#fff;font-size:12px;letter-spacing:.2px;white-space:nowrap}

  .brand{position:absolute;left:60px;top:92px;color:var(--blue-main);font-weight:700}
  .brand__name{font-size:74px;line-height:1;letter-spacing:2px}
  .brand__sub{font-size:16px;letter-spacing:1.6px;margin-top:4px}

  .address{position:absolute;left:120px;top:218px;color:var(--ink);font-size:15px;line-height:1.35;font-style:normal}
  .contacts{position:absolute;left:120px;top:290px;color:var(--ink);font-size:14px;list-style:none;line-height:1.45}
  .contacts li{display:flex;align-items:center;gap:8px;white-space:nowrap}
  .contacts svg{width:13px;height:13px;flex:none}

  .person{position:absolute;right:34px;top:64px;text-align:right}
  .person__name{color:var(--blue-main);font-weight:700;font-size:20px;letter-spacing:.5px}
  .person__role{color:var(--green);font-size:16px;margin-top:3px}

  .brand--back{left:0;right:0;top:120px;text-align:center;color:#fff}
  .brand--back .brand__name{font-size:96px}
  .brand--back .brand__sub{font-size:21px;letter-spacing:2.4px}
  .web-back{position:absolute;left:0;right:0;top:300px;text-align:center;color:#fff;font-size:14px;letter-spacing:5px}
</style>
</head>
<body>
  <section class="card card--front" aria-label="Business card front">
    <svg class="front-band" viewBox="0 0 700 400" aria-hidden="true">
      <polygon points="0,368 412,368 452,290 700,290 700,296 456,296 416,374 0,374" fill="var(--green)"/>
      <polygon points="0,380 420,380 460,302 700,302 700,400 0,400" fill="var(--blue-main)"/>
    </svg>

    <div class="brand">
      <div class="brand__name">VELRAN</div>
      <div class="brand__sub">GLOBAL COMPONENTS</div>
    </div>

    <address class="address">
      17 Marlow Yard, Upper Heath<br>
      Warwick, CV31 8QL<br>
      United Kingdom
    </address>

    <ul class="contacts">
      <li>
        <svg viewBox="0 0 16 16"><path d="M4 1l3 3-2 2c1 2 3 4 5 5l2-2 3 3-2 3C7 15 1 9 1 3z" fill="var(--blue-main)"/></svg>
        020 7946 0381
      </li>
      <li>
        <svg viewBox="0 0 16 16"><rect x="3" y="1" width="10" height="14" rx="1.5" fill="none" stroke="var(--blue-main)" stroke-width="2"/></svg>
        020 7946 0725
      </li>
      <li>
        <svg viewBox="0 0 16 16"><rect x="1" y="3" width="14" height="10" fill="var(--blue-main)"/><path d="M1 3l7 6 7-6" fill="none" stroke="#fff" stroke-width="1.4"/></svg>
        dorian@velrancomponents-example.co.uk
      </li>
    </ul>

    <div class="person">
      <div class="person__name">DORIAN HALE</div>
      <div class="person__role">CEO/Founder</div>
    </div>

    <div class="web-front">www.velrancomponents-example.co.uk</div>
  </section>

  <section class="card card--back" aria-label="Business card back">
    <div class="brand brand--back">
      <div class="brand__name">VELRAN</div>
      <div class="brand__sub">GLOBAL COMPONENTS</div>
    </div>
    <div class="web-back">www.velrancomponents-example.co.uk</div>
  </section>
</body>
</html>
```